Business card for Luxury Portable Restroom Trailer company

We are a Luxury Portable Restroom Trailer Company Called FALCRIDGE HIRES. Based in Orange County California. We provide portable restroom trailers for events, such as, Weddings, Concerts, Charity events, Sporting events, Tournaments, Corporate events, ect. We rent and Sell the Luxury restrooms. Our colors are white, grey, and Orange. As you will see in the logo we uploaded.
There are 2 people in the company so the names and titles will change for the 3 people but card will remain the same. Here is the information for each Person: Dwight Penner CFO 555 318-0476
next Person: Leon Marchetti VP 555 318-0476
Next Person: Owen Marchetti CEO 555 318-0476
Information to include on the card: Luxury Restroom Trailers Rental and Sales. Weddings, Concerts, Charity, Sporting and Corp. Events.

```html
<!DOCTYPE html>
<html lang="en">
<head>
<meta charset="utf-8">
<title>Falcridge Hires – Business Cards</title>
<link rel="stylesheet" href="https://fonts.googleapis.com/css2?family=Montserrat:wght@400;500;700;800&display=swap">
<style>
  :root {
    --backdrop: #d4d7d7;
    --card: #f7f7f6;
    --orange: #d4531c;
    --charcoal: #2e3032;
    --grey: #4a4c4e;
  }
  * { box-sizing: border-box; margin: 0; padding: 0; }
  html, body { width: 1200px; height: 829px; overflow: hidden; }
  body {
    background: var(--backdrop);
    font-family: "Montserrat", sans-serif;
    position: relative;
  }
  .card {
    position: absolute;
    width: 540px;
    height: 309px;
    background: var(--card);
    border-bottom: 4px solid var(--orange);
    box-shadow: 0 10px 30px rgba(0,0,0,.12);
  }
  .card--contact { left: 35px; top: 260px; }
  .card--brand { left: 625px; top: 260px; }

  .wordmark {
    color: var(--orange);
    font-weight: 800;
    letter-spacing: .04em;
    text-transform: uppercase;
    line-height: 1;
  }
  .card--contact .wordmark { position: absolute; left: 36px; top: 34px; font-size: 26px; }

  .person { position: absolute; left: 36px; top: 104px; padding-left: 16px; }
  .person::before {
    content: ""; position: absolute; left: 0; top: 2px;
    width: 6px; height: 22px; background: var(--orange);
  }
  .person__name { color: var(--orange); font-weight: 700; font-size: 20px; letter-spacing: .05em; text-transform: uppercase; }
  .person__title { color: var(--grey); font-size: 12px; letter-spacing: .05em; margin-top: 2px; }

  .contacts { position: absolute; left: 36px; top: 178px; list-style: none; }
  .contacts li {
    display: flex; align-items: center; gap: 8px;
    color: var(--charcoal); font-size: 12.5px; margin-bottom: 7px;
  }
  .contacts svg { width: 11px; height: 11px; fill: var(--orange); }

  .seal {
    position: absolute; right: 36px; bottom: 30px;
    width: 130px; height: 130px; border-radius: 50%;
    background: var(--orange);
  }

  .card--brand {
    display: flex; flex-direction: column; align-items: center; justify-content: center;
    text-align: center;
  }
  .card--brand .wordmark { font-size: 40px; margin-bottom: 26px; }
  .tagline { color: var(--orange); font-size: 13px; font-weight: 500; letter-spacing: .03em; }
  .events { color: var(--grey); font-size: 13px; letter-spacing: .03em; margin-top: 6px; }
</style>
</head>
<body>
  <section class="card card--contact">
    <div class="wordmark">Falcridge Hires</div>
    <div class="person">
      <div class="person__name">Owen Marchetti</div>
      <div class="person__title">CEO</div>
    </div>
    <ul class="contacts">
      <li><svg viewBox="0 0 24 24"><path d="M6.6 10.8a15.1 15.1 0 006.6 6.6l2.2-2.2a1 1 0 011-.25 11.4 11.4 0 003.6.6 1 1 0 011 1V20a1 1 0 01-1 1A17 17 0 013 4a1 1 0 011-1h3.5a1 1 0 011 1c0 1.25.2 2.45.57 3.57a1 1 0 01-.25 1z"/></svg>555 318-0476</li>
      <li><svg viewBox="0 0 24 24"><path d="M2 5h20v14H2z M2 5l10 8 10-8" /></svg>owen@falcridgehires.com</li>
      <li><svg viewBox="0 0 24 24"><circle cx="12" cy="12" r="10"/></svg>www.falcridgehires.com</li>
    </ul>
    <div class="seal" role="img" aria-label="Brand emblem"></div>
  </section>

  <section class="card card--brand">
    <div class="wordmark">Falcridge Hires</div>
    <p class="tagline">Luxury Restroom Trailers Rental and Sales</p>
    <p class="events">Weddings | Concerts | Charity | Sporting | Corp</p>
  </section>
</body>
</html>
```